Blue Heron Journeys

We are a predominantly online travel agency with high-end (first/business class) clients. I'm looking to either have our existing logo revamped or a new logo created with business card layout. I prefer to work with existing logo if possible so it remains familiar with existing clientele. I have uploaded a yellow business card layout showing icons on one side of the card. I would like to keep my existing colours, not yellow. could the company name/tag line go over the icons?
Industry/Entity Type
Business
Contact Information for Business Card
Lucinda Fairley
Director
(I.A.T.A. 07715463)
(Corvano Pty. Ltd) ABN 61 574 203 918
512/18 Kendrick Lane
Wattle Reach | NSW 2577 | Australia
www.blueheronjourneys.com.au
m: + 61 (0) 417 588 130
t: + 61 (0) 2 9416 2058
e: lucinda@blueheronjourneys.com.au

```html
<!DOCTYPE html>
<html lang="en">
<head>
<meta charset="utf-8">
<title>Blue Heron Journeys – Business Card</title>
<link rel="stylesheet" href="https://fonts.googleapis.com/css2?family=Exo+2:wght@400;600&family=Noticia+Text:wght@400&display=swap">
<style>
  :root {
    --backdrop: #1b1c1c;
    --peach: #fccb98;
    --peach-deep: #f7b98a;
    --charcoal: #3a3a3c;
    --ink: #2e2e30;
    --ink-soft: #4a4a4c;
    --card-white: #ffffff;
    --accent-line: #fcc98f;
  }
  * { box-sizing: border-box; margin: 0; padding: 0; }
  html, body {
    width: 1200px; height: 1000px; overflow: hidden;
    background: var(--backdrop);
  }
  .stage {
    position: relative; width: 1200px; height: 1000px;
    display: flex; flex-direction: column; align-items: center; justify-content: center;
    gap: 56px;
  }
  .card {
    position: relative; width: 600px; height: 343px;
    border-radius: 18px; overflow: hidden;
  }

  /* Front */
  .card-front { background: var(--peach); }
  .icon-pattern {
    position: absolute; inset: 0;
    background: linear-gradient(135deg, var(--peach) 0%, var(--peach-deep) 50%, var(--peach) 100%);
  }
  .brand-disc {
    position: absolute; width: 410px; height: 410px; border-radius: 50%;
    left: 130px; top: -34px; background: var(--charcoal);
    display: flex; align-items: center; justify-content: center;
  }
  .brand-name {
    font-family: "Noticia Text", serif; font-weight: 400;
    font-size: 38px; color: var(--peach); letter-spacing: 0.5px;
    text-align: center;
  }

  /* Back */
  .card-back { background: var(--card-white); color: var(--ink); font-family: "Exo 2", sans-serif; }
  .corner-accent {
    position: absolute; left: 30px; top: 24px; width: 76px; height: 44px;
    background: var(--peach);
    opacity: 0.85;
  }
  .person {
    position: absolute; right: 34px; top: 58px; text-align: right;
  }
  .person-name {
    font-family: "Noticia Text", serif; font-weight: 400; font-size: 36px; color: var(--ink); line-height: 1.05;
  }
  .person-role { font-size: 19px; color: var(--ink-soft); }
  .registration {
    position: absolute; left: 34px; top: 150px;
    font-size: 15px; line-height: 1.35; color: var(--ink-soft);
  }
  .contact {
    position: absolute; left: 34px; top: 214px;
    font-size: 15.5px; line-height: 1.35; color: var(--ink-soft);
  }
  .contact b { font-weight: 600; color: var(--ink); }
  .divider {
    position: absolute; right: 34px; top: 232px; width: 250px; height: 2px;
    background: var(--accent-line);
  }
  .address {
    position: absolute; right: 34px; top: 250px; text-align: right;
    font-size: 15.5px; line-height: 1.35; color: var(--ink-soft);
  }
</style>
</head>
<body>
<main class="stage">
  <section class="card card-front">
    <div class="icon-pattern" role="img" aria-label="Pattern of line-drawn travel icons: landmarks, globes, planes, luggage and trees"></div>
    <div class="brand-disc">
      <h1 class="brand-name">Blue Heron Journeys</h1>
    </div>
  </section>

  <section class="card card-back">
    <div class="corner-accent" role="img" aria-label="Small grid of peach squares"></div>
    <div class="person">
      <h2 class="person-name">Lucinda Fairley</h2>
      <p class="person-role">Director</p>
    </div>
    <div class="registration">
      <p>(I.A.T.A. 07715463)</p>
      <p>(Corvano Pty. Ltd) ABN 61 574 203 918</p>
    </div>
    <div class="contact">
      <p><b>M:</b> + 61 (0) 417 588 130</p>
      <p><b>T:</b> + 61 (0) 2 9416 2058</p>
      <p><b>E:</b> lucinda@blueheronjourneys.com.au</p>
    </div>
    <div class="divider"></div>
    <div class="address">
      <p>512/18 Kendrick Lane</p>
      <p>Wattle Reach | NSW 2577 | Australia</p>
      <p>www.blueheronjourneys.com.au</p>
    </div>
  </section>
</main>
</body>
</html>
```